Corvane Paintless Dent Removal

Our company works on vehicles removing dents using a highly skilled trade which the metal is massaged out with special tools without disturbing the original paint, hence paintless dent removal. Besides keeping the paint and metal original its also very environmentally friendly since no paint or toxic fillers are used. Also we we are one of the most experienced companies in the business with 25 years

Target Market(s)

Retail Automobile consumers, Auto Dealerships and Auto Body Shops

Industry/Entity Type

Auto Repair

Contact Information for Business Card

Dale Hollister
PO Box 518 Brookmere, NY 11962
631-555-0148
corvanepdr@mailbox-example.com
website corvanepdr.example
reelhub corvane paintless dent removal
25 years of experience removing Dents, Dings and Hail Damage

Font styles to use
Serif
Sans Serif

Colors

Designer to choose colors to be used in the design.

Requirements
Must have
• I do like things that are simple but classy and somewhat bold, also I like my logo so that should be somewhat important

```html
<!DOCTYPE html>
<html lang="en">
<head>
<meta charset="UTF-8">
<title>Corvane Paintless Dent Removal — Business Card</title>
<link href="https://fonts.googleapis.com/css2?family=Work+Sans:wght@400;500;600;700&display=swap" rel="stylesheet">
<style>
  :root {
    --backdrop: #3a2f2a;
    --card: #1a1a1a;
    --card-edge: #232323;
    --ink: #f2f2f2;
    --ink-soft: #d6d6d6;
    --silver: #b9b9b9;
    --accent: #6cc24a;
  }
  * { box-sizing: border-box; margin: 0; padding: 0; }
  html, body {
    width: 1200px; height: 715px; overflow: hidden;
    background: var(--backdrop);
    font-family: "Work Sans", Arial, sans-serif;
  }
  .stage {
    position: relative; width: 1200px; height: 715px;
    display: flex; align-items: center; justify-content: center; gap: 40px;
  }
  .card {
    position: relative; width: 540px; height: 309px;
    background: linear-gradient(160deg, var(--card-edge), var(--card));
    box-shadow: 0 14px 30px rgba(0,0,0,.45);
    color: var(--ink);
  }
  /* front face */
  .card-front .brand {
    position: absolute; left: 0; right: 0; top: 96px;
    text-align: center;
    font-size: 40px; font-weight: 700; letter-spacing: 1px;
    color: var(--silver); line-height: 1.1;
  }
  .card-front .brand small {
    display: block; font-size: 17px; letter-spacing: .5px; margin-top: 4px;
  }
  .card-front .tagline {
    position: absolute; left: 34px; bottom: 30px;
    font-size: 12.5px; line-height: 1.45; color: var(--ink-soft);
  }
  .card-front .tagline .channel { color: var(--accent); }
  /* back face */
  .card-back .brand {
    position: absolute; left: 26px; top: 108px; width: 230px;
    font-size: 30px; font-weight: 700; line-height: 1.1; color: var(--ink);
    text-align: center;
  }
  .card-back .brand small { display: block; font-size: 14px; margin-top: 4px; }
  .card-back .divider {
    position: absolute; left: 282px; top: 70px; width: 2px; height: 160px;
    background: var(--accent);
  }
  .card-back .contact {
    position: absolute; left: 304px; top: 80px;
    font-size: 13.5px; line-height: 1.5; color: var(--ink-soft);
  }
  .contact .name {
    font-size: 19px; font-weight: 600; letter-spacing: 1.5px;
    text-transform: uppercase; color: var(--ink); line-height: 1.2;
  }
  .contact .role { margin-bottom: 6px; }
  .contact .row { display: flex; align-items: center; gap: 7px; }
  .contact .row svg { width: 10px; height: 10px; flex: none; }
  .contact .web-domain { color: var(--accent); }
</style>
</head>
<body>
<main class="stage">
  <section class="card card-front">
    <div class="brand">CORVANE<small>Paintless Dent Removal</small></div>
    <p class="tagline">
      <span class="channel">reelhub</span> corvane paintless dent removal<br>
      25 years of experience removing Dents, Dings and Hail Damage
    </p>
  </section>

  <section class="card card-back">
    <div class="brand">CORVANE<small>Paintless Dent Removal</small></div>
    <div class="divider"></div>
    <div class="contact">
      <div class="name">Dale Hollister</div>
      <div class="role">President</div>
      <div>PO Box 518</div>
      <div>Brookmere, NY 11962</div>
      <div class="row">
        <svg viewBox="0 0 10 10" aria-hidden="true"><path d="M2 1 L4 1 L4.6 3 L3.4 3.8 Q4.3 5.8 6.2 6.6 L7 5.4 L9 6 L9 8 Q9 9 8 9 Q1 8.4 1 2 Q1 1 2 1Z" fill="#f2f2f2"/></svg>
        631-555-0148
      </div>
      <div class="row">
        <svg viewBox="0 0 10 10" aria-hidden="true"><rect x="0.6" y="2" width="8.8" height="6" fill="none" stroke="#f2f2f2" stroke-width="1"/><path d="M0.6 2 L5 5.4 L9.4 2" fill="none" stroke="#f2f2f2" stroke-width="1"/></svg>
        corvanepdr@mailbox-example.com
      </div>
      <div class="row">
        <svg viewBox="0 0 10 10" aria-hidden="true"><circle cx="5" cy="5" r="4.2" fill="none" stroke="#f2f2f2" stroke-width="1"/><path d="M0.8 5 H9.2 M5 0.8 Q2.6 5 5 9.2 M5 0.8 Q7.4 5 5 9.2" fill="none" stroke="#f2f2f2" stroke-width=".8"/></svg>
        <span>www.<span class="web-domain">corvanepdr</span>.example</span>
      </div>
    </div>
  </section>
</main>
</body>
</html>
```